FinTech company looking to revamp and expand client-facing interface for our financial models

Pellworth Engines currently has a very simple website that allows clients to interact with our financial models. We are looking to completely redesign the current site and add several extra pages to provide extra functionality. We want the design to have a modern, slick feel, that will work on both a desktop or a tablet. It should be straightforward for clients to move between different pages at any time, and clear from the layout how to interact with the more advanced features. We have included screenshots of existing pages in the attached design brief, as well as sketches of the functionality required by the new pages, but can't provide a direct link to the current site.
Target Market(s)
Professional investors that will be paying to access the interface
Industry/Entity Type
Finance
Number of Pages Required
4 page
Colors
Designer to choose colors to be used in the design.
Look and feel
Each slider illustrates characteristics of the customer's brand and the style your logo design should communicate.

```html
<!DOCTYPE html>
<html lang="en">
<head>
<meta charset="utf-8">
<title>Pellworth Engines – Models</title>
<link rel="stylesheet" href="https://fonts.googleapis.com/css2?family=Work+Sans:wght@400;500;600;700&display=swap">
<style>
:root{
  --page:#ecebe9;
  --navy:#2a2f4b;
  --head-row:#1f2339;
  --row-a:#343a58;
  --row-b:#3d4466;
  --footer:#21253c;
  --cyan:#35dfe6;
  --orange:#f5852c;
  --white:#ffffff;
  --ink:#1f2336;
  --muted:#4a4f63;
  --tab-bg:#ecebe9;
  --line:rgba(255,255,255,.08);
}
*{box-sizing:border-box;margin:0;padding:0}
html,body{width:1118px;height:1200px;overflow:hidden}
body{background:var(--page);font-family:"Work Sans",sans-serif;position:relative}
.screen{position:absolute;left:93px;width:932px;height:529px;background:var(--navy);overflow:hidden}
.screen--models{top:56px}
.screen--factors{top:615px}
.topbar{position:absolute;left:0;top:0;width:100%;height:40px;background:var(--white);display:flex;align-items:center}
.brand{position:absolute;left:34px;top:0;line-height:40px;font-weight:700;font-size:14.5px;color:var(--ink);letter-spacing:.2px}
.tab{position:absolute;top:0;height:40px;line-height:40px;font-size:8.5px;color:var(--ink)}
.tab--active{background:var(--tab-bg);width:47px;text-align:center;left:133px}
.nav-item{position:absolute;top:0;height:40px;display:flex;align-items:center;gap:6px;font-size:8px;letter-spacing:.3px;color:var(--muted)}
.nav-item svg{width:9px;height:9px;fill:var(--ink)}
.nav-item--active{background:var(--tab-bg);left:622px;width:67px;justify-content:center}
.dropdown{position:absolute;left:622px;top:40px;width:85px;height:97px;background:var(--tab-bg);padding-top:9px}
.dropdown li{list-style:none;display:flex;align-items:center;gap:9px;padding-left:12px;height:16.8px;font-size:8px;color:var(--muted);letter-spacing:.3px}
.dropdown svg{width:5px;height:6px;stroke:var(--ink);fill:none;stroke-width:1.6}
.filter{position:absolute;display:flex;align-items:center;font-size:8.5px}
.filter .key{color:var(--cyan)}
.filter .hint{color:#b9bccb}
.field{position:absolute;height:17px;width:92px;border-radius:9px;background:#f1f1f3;font-size:7.5px;color:var(--ink);line-height:17px;padding-left:12px}
.export{position:absolute;width:80px;height:22px;border-radius:11px;background:#353b5c;border:1px solid #4b5378;display:flex;align-items:center;justify-content:center;gap:6px;color:#e8e9f0;font-size:8.5px;box-shadow:0 3px 8px rgba(0,0,0,.25)}
.export svg{width:9px;height:9px;stroke:var(--cyan);fill:none;stroke-width:1.6}
.grid{position:absolute;top:196px;border-collapse:collapse;table-layout:fixed;font-size:9px;color:var(--white)}
.grid th{height:34px;background:var(--head-row);text-align:left;font-weight:500;padding-left:12px;border-right:1px solid var(--line)}
.grid td{height:45px;padding-left:12px;line-height:15px;border-right:1px solid var(--line);border-top:1px solid rgba(0,0,0,.12);font-weight:500}
.grid tbody tr:nth-child(odd) td{background:var(--row-a)}
.grid tbody tr:nth-child(even) td{background:var(--row-b)}
.grid .id{color:var(--cyan);font-size:8.5px;padding-left:9px}
.grid th.id{color:var(--cyan)}
.grid .factor{color:var(--orange)}
.grid--models{left:34px;width:863px}
.grid--factors{left:144px;width:644px}
.sort{display:inline-block;margin-left:12px;width:0;height:0;border-left:3.5px solid transparent;border-right:3.5px solid transparent;border-top:4px solid var(--cyan);vertical-align:middle}
.footer{position:absolute;left:0;bottom:0;width:100%;height:29px;background:var(--footer);color:#e4e5ec;font-size:5.5px;display:flex;align-items:center;justify-content:center}
.footer .code{position:absolute;right:30px;top:9px;font-size:5.5px}
</style>
</head>
<body>

<section class="screen screen--models">
  <header class="topbar">
    <div class="brand">PELLWORTH</div>
    <span class="tab tab--active">250D</span>
    <span class="tab" style="left:198px">83D</span>
    <span class="tab" style="left:244px">42D</span>
    <span class="nav-item nav-item--active"><svg viewBox="0 0 10 10"><path d="M5 1 0 5h1.5v4h2.5V6.5h2V9h2.5V5H10z"/></svg>MODELS</span>
    <span class="nav-item" style="left:706px"><svg viewBox="0 0 10 10"><path d="M4 0h2l.3 1.4 1.2.7 1.4-.5 1 1.7-1.1 1v1.4l1.1 1-1 1.7-1.4-.5-1.2.7L6 10H4l-.3-1.4-1.2-.7-1.4.5-1-1.7 1.1-1V4.3L.1 3.3l1-1.7 1.4.5 1.2-.7zM5 3.3a1.7 1.7 0 1 0 0 3.4 1.7 1.7 0 0 0 0-3.4z"/></svg>SENDITIVITIES</span>
    <span class="nav-item" style="left:806px"><svg viewBox="0 0 10 10"><path d="M5 .3 6.4 3.5 9.8 3.8 7.2 6l.8 3.4L5 7.6 2 9.4 2.8 6 .2 3.8l3.4-.3z"/></svg>FAVOURITES</span>
  </header>
  <ul class="dropdown">
    <li><svg viewBox="0 0 5 6"><path d="M1 .5 3.5 3 1 5.5"/></svg>EQUITIES</li>
    <li><svg viewBox="0 0 5 6"><path d="M1 .5 3.5 3 1 5.5"/></svg>ETFS</li>
    <li><svg viewBox="0 0 5 6"><path d="M1 .5 3.5 3 1 5.5"/></svg>PAIRS</li>
    <li><svg viewBox="0 0 5 6"><path d="M1 .5 3.5 3 1 5.5"/></svg>ETF PAIRS</li>
    <li><svg viewBox="0 0 5 6"><path d="M1 .5 3.5 3 1 5.5"/></svg>FACTORS</li>
  </ul>

  <div class="filter" style="left:36px;top:65px"><span class="key">Quality :</span><span class="hint" style="margin-left:15px">Threshold</span></div>
  <div class="field" style="left:135px;top:63px">-10</div>
  <div class="filter" style="left:36px;top:98px"><span class="key">Abs. Stat :</span><span class="hint" style="margin-left:6px">Threshold</span></div>
  <div class="field" style="left:135px;top:96px">-10</div>
  <div class="export" style="left:36px;top:142px"><svg viewBox="0 0 10 10"><path d="M8 6v3H1V2h3M6 1h3v3M9 1 4.5 5.5"/></svg>Export</div>

  <table class="grid grid--models">
    <colgroup><col style="width:52px"><col style="width:103px"><col style="width:80px"><col style="width:80px"><col style="width:69px"><col style="width:69px"><col style="width:74px"><col style="width:72px"><col style="width:69px"><col style="width:66px"><col style="width:66px"><col style="width:63px"></colgroup>
    <thead><tr><th class="id" style="padding-left:16px">ID</th><th>Sector</th><th>Time</th><th>Quality</th><th>Stat1</th><th>Stat2</th><th>Stat3</th><th>Stat4</th><th>Stat5</th><th>Stat6</th><th>Stat7</th><th>Stat8</th></tr></thead>
    <tbody>
      <tr><td class="id">Model1</td><td>Materials</td><td>2019-07-03<br>12:15:00.000</td><td>30.2288</td><td>2.01574</td><td>23.305</td><td>-0.149368</td><td>22.3054</td><td>4.01574</td><td>0.149368</td><td>2.819368</td><td>2.60858</td></tr>
      <tr><td class="id">Model2</td><td>Industrials</td><td>2019-07-03<br>12:15:00.000</td><td>32.8694</td><td>0.87307</td><td>32.185</td><td>-0.0336927</td><td>33.9911</td><td>11.87307</td><td>-0.472968</td><td>-0.832968</td><td>6.80646</td></tr>
      <tr><td class="id">Model3</td><td>Customer<br>Discretionary</td><td>2019-07-03<br>12:15:00.000</td><td>1.66002</td><td>0.569222</td><td>159.814</td><td>0.0234587</td><td>172.616</td><td>10.5692</td><td>-0.750396</td><td>-0.38039</td><td>4.69146</td></tr>
      <tr><td class="id">Model4</td><td>Information<br>Technology</td><td>2019-07-03<br>12:15:00.000</td><td>45.6856</td><td>0.412148</td><td>202.488</td><td>0.00654765</td><td>205.834</td><td>11.91210</td><td>-0.137913</td><td>0.449595</td><td>3.85106</td></tr>
      <tr><td class="id">Model5</td><td>Information<br>Technology</td><td>2019-07-03<br>12:15:00.000</td><td>75.7733</td><td>7.06728</td><td>188.605</td><td>0.016789</td><td>181.665</td><td>3.082241</td><td>0.981019</td><td>1.29847</td><td>3.34927</td></tr>
    </tbody>
  </table>

  <footer class="footer">© 2019 | www.pellworthengines.com<span class="code">M1</span></footer>
</section>

<section class="screen screen--factors">
  <header class="topbar">
    <div class="brand">PELLWORTH</div>
    <span class="tab tab--active">250D</span>
    <span class="tab" style="left:198px">83D</span>
    <span class="tab" style="left:244px">42D</span>
    <span class="nav-item nav-item--active"><svg viewBox="0 0 10 10"><path d="M5 1 0 5h1.5v4h2.5V6.5h2V9h2.5V5H10z"/></svg>MODELS</span>
    <span class="nav-item" style="left:706px"><svg viewBox="0 0 10 10"><path d="M4 0h2l.3 1.4 1.2.7 1.4-.5 1 1.7-1.1 1v1.4l1.1 1-1 1.7-1.4-.5-1.2.7L6 10H4l-.3-1.4-1.2-.7-1.4.5-1-1.7 1.1-1V4.3L.1 3.3l1-1.7 1.4.5 1.2-.7zM5 3.3a1.7 1.7 0 1 0 0 3.4 1.7 1.7 0 0 0 0-3.4z"/></svg>SENDITIVITIES</span>
    <span class="nav-item" style="left:806px"><svg viewBox="0 0 10 10"><path d="M5 .3 6.4 3.5 9.8 3.8 7.2 6l.8 3.4L5 7.6 2 9.4 2.8 6 .2 3.8l3.4-.3z"/></svg>FAVOURITES</span>
  </header>

  <div class="filter" style="left:144px;top:62px"><span class="key">Stat1</span><span class="hint" style="margin-left:3px">Threshold</span></div>
  <div class="field" style="left:218px;top:59px">-10</div>
  <div class="filter" style="left:144px;top:84px"><span class="key">Stat2</span><span class="hint" style="margin-left:3px">Threshold</span></div>
  <div class="field" style="left:218px;top:83px">-10</div>
  <div class="filter" style="left:144px;top:106px"><span class="key">Stat3</span><span class="hint" style="margin-left:3px">Threshold</span></div>
  <div class="field" style="left:218px;top:106px">-10</div>
  <div class="export" style="left:146px;top:142px"><svg viewBox="0 0 10 10"><path d="M8 6v3H1V2h3M6 1h3v3M9 1 4.5 5.5"/></svg>Export</div>

  <table class="grid grid--factors">
    <colgroup><col style="width:75px"><col style="width:51px"><col style="width:92px"><col style="width:75px"><col style="width:68px"><col style="width:74px"><col style="width:68px"><col style="width:67px"><col style="width:74px"></colgroup>
    <thead><tr><th class="factor">Factor</th><th class="id" style="padding-left:12px">ID<span class="sort"></span></th><th>Sector</th><th style="padding-left:20px">Stat1</th><th style="padding-left:15px">Stat2</th><th style="padding-left:22px">Stat3</th><th style="padding-left:19px">Stat4</th><th style="padding-left:18px">Stat5</th><th style="padding-left:17px">Stat6</th></tr></thead>
    <tbody>
      <tr><td class="factor">Factor1</td><td class="id">Model1</td><td>Materials</td><td style="padding-left:20px">-1.4</td><td style="padding-left:15px">0.1</td><td style="padding-left:19px">-3.1</td><td style="padding-left:22px">0.7</td><td style="padding-left:18px">30.2</td><td style="padding-left:18px">0.9</td></tr>
      <tr><td class="factor">Factor2</td><td class="id">Model1</td><td>Materials</td><td style="padding-left:20px">2.8</td><td style="padding-left:15px">0.1</td><td style="padding-left:19px">6.1</td><td style="padding-left:22px">100</td><td style="padding-left:18px">30.2</td><td style="padding-left:18px">0.9</td></tr>
      <tr><td class="factor">Factor3</td><td class="id">Model1</td><td>Materials</td><td style="padding-left:20px">-3.7</td><td style="padding-left:15px">2.7</td><td style="padding-left:19px">-7.2</td><td style="padding-left:22px">100</td><td style="padding-left:18px">30.2</td><td style="padding-left:18px">0.9</td></tr>
      <tr><td class="factor">Factor1</td><td class="id">Model2</td><td>Industrials</td><td style="padding-left:20px">2.8</td><td style="padding-left:15px">0.2</td><td style="padding-left:19px">2.7</td><td style="padding-left:22px">0.5</td><td style="padding-left:18px">32.9</td><td style="padding-left:18px">0.5</td></tr>
      <tr><td class="factor">Factor2</td><td class="id">Model2</td><td>Industrials</td><td style="padding-left:20px">0.8</td><td style="padding-left:15px">0.2</td><td style="padding-left:19px">2.5</td><td style="padding-left:22px">0.5</td><td style="padding-left:18px">32.9</td><td style="padding-left:18px">0.5</td></tr>
    </tbody>
  </table>

  <footer class="footer">© 2019 | www.pellworthengines.com<span class="code">M1</span></footer>
</section>

</body>
</html>
```